Meadow Gate Labradoodle web design

We're a new labradoodle breeder in Charleston, SC in need of a web design.

Our name is Meadow Gate Labradoodles.

Site we like: http://www.pebblefieldlabradoodles.com/
http://www.quillbrookfarmlabradoodles.com/

Logo Font:
The ''Meadow Gate'' font is called TestarossaNF and is available freely at http://www.glyphtrove.com/velmorina-nf.font.  The ''Labradoodles'' font is called Worstveld Sling Extra and is available freely at http://www.typebasketzone.com/KorvandelHookExtra.php.

Requirements
Must have
• Our logo
1. Home page
2. Labradoodle F.A.Q.
3. Our doodles
4. Availability
5. Adoption Process
6. Contact us
Link/badge icon for Health Guarantee
Nice to have
• Color and font to match the logo.

An area to add pictures
Should not have
• Rainbows
Rainbow colors

```html
<!DOCTYPE html>
<html lang="en">
<head>
<meta charset="utf-8">
<title>Meadow Gate Labradoodles</title>
<link href="https://fonts.googleapis.com/css2?family=Federo&family=Oswald:wght@500&family=Titillium+Web:wght@300;400&display=swap" rel="stylesheet">
<style>
:root{
  --wood:#3d3d3b;
  --wood-dark:#2b2b2a;
  --pink:#e0607a;
  --brown:#6b4a2c;
  --tan:#dcc3a3;
  --tan-dark:#b89a76;
  --text:#666;
  --hero-top:#c9c9c9;
  --footer:#606060;
  --footer-text:#f1f1f1;
  --rule:#d8d8d8;
}
*{box-sizing:border-box;margin:0;padding:0}
html,body{width:1200px;height:909px;overflow:hidden;background:#fff}
body{position:relative;font-family:"Titillium Web",sans-serif;color:var(--text)}
.abs{position:absolute}
.display{font-family:"Federo",sans-serif}

.header-band{left:0;top:0;width:1200px;height:104px;background:repeating-linear-gradient(180deg,var(--wood) 0 22px,var(--wood-dark) 22px 24px)}
.hero{left:0;top:104px;width:1200px;height:290px;background:linear-gradient(180deg,var(--hero-top),#e6e6e6 55%,#fff)}

.brand{left:189px;top:4px;width:140px;height:118px;display:flex;flex-direction:column;align-items:center;justify-content:center;gap:6px}
.brand-dot{width:64px;height:64px;border-radius:50%;background:var(--pink)}
.brand-name{font-family:"Titillium Web",sans-serif;font-weight:400;font-size:13px;line-height:1.1;color:#fff;text-align:center}

.nav{left:514px;top:62px;display:flex;gap:2px}
.nav a{display:block;height:39px;line-height:39px;padding:0 15px;background:linear-gradient(#2a2a2a,#111);color:#fff;font-family:"Oswald",sans-serif;font-size:15px;text-decoration:none;border-radius:2px;box-shadow:0 2px 3px rgba(0,0,0,.4)}

.hero-title{left:196px;top:162px;font-size:42px;line-height:42px;color:var(--pink)}
.hero-sub{left:196px;top:266px;font-size:17px;color:var(--pink)}
.hero-copy{left:196px;top:290px;width:320px;font-size:9.5px;line-height:11.6px;color:#555}

.btn{display:inline-block;height:26px;line-height:26px;padding:0 12px;background:linear-gradient(var(--tan),#cfb28d);color:var(--brown);font-family:"Federo",sans-serif;font-size:12px;border-radius:2px;box-shadow:0 3px 0 var(--tan-dark);text-decoration:none}

.dog-photo{left:700px;top:128px;width:156px;height:252px;border-radius:70px 70px 30px 30px;background:radial-gradient(ellipse at 50% 40%,#c99a66,#b07b47 70%,rgba(176,123,71,0))}
.grass-photo{left:722px;top:102px;width:398px;height:140px;border-radius:0 0 60% 40%;background:linear-gradient(180deg,#7f9a2c,#a6b74a 60%,rgba(166,183,74,0))}
.dots{left:936px;top:367px;display:flex;gap:4px}
.dots span{width:12px;height:12px;border-radius:50%;background:#d4d4d4}
.dots span:first-child{background:var(--pink)}

.col-title{font-size:19px;line-height:23px;color:var(--brown)}
.benefits{left:198px;top:436px;width:170px}
.benefits ul{list-style:none;margin-top:10px}
.benefits li{position:relative;padding:4px 0 4px 14px;font-size:11px;line-height:13.5px;border-bottom:1px dotted var(--rule)}
.benefits li:last-child{border:0}
.paw{position:absolute;left:0;top:7px;width:8px;height:8px}

.divider{top:458px;height:190px;border-left:1px dotted #ccc}
.welcome{left:455px;top:436px;width:232px}
.welcome p{margin-top:9px;font-size:11px;line-height:13.4px}

.principles{left:748px;top:436px;width:245px}
.principle{position:relative;padding-left:25px;margin-bottom:14px}
.principle h3{font-size:14px;color:var(--brown);font-weight:400}
.principle p{font-size:11px;line-height:13.4px;margin-top:4px}
.principle .paw-big{position:absolute;left:0;top:1px;width:16px;height:16px}

.seal{left:932px;top:674px;width:62px;height:62px}

.footer{left:0;top:726px;width:1200px;height:183px;background:var(--footer);color:var(--footer-text)}
.ftitle{font-size:16px;color:#fff}
.f-gallery{left:198px;top:22px;width:205px}
.f-gallery p{font-size:9.5px;line-height:11.6px;margin:10px 0 10px}
.f-links{left:451px;top:22px;width:125px}
.f-links a{display:block;font-size:11px;color:#eee;text-decoration:none;padding:4px 0 5px;border-bottom:1px dotted #808080}
.f-connect{left:630px;top:22px;width:200px}
.social{display:flex;gap:8px;margin:11px 0 8px}
.social span{width:24px;height:24px;border-radius:50%;background:var(--pink)}
.news-title{font-size:15px;color:#fff}
.news-label{font-size:9.5px;color:#8f8f8f;text-transform:uppercase}
.news-row{display:flex;margin-top:1px}
.news-row input{width:146px;height:20px;border:0;background:#fff}
.news-row button{width:46px;height:20px;border:0;background:var(--pink);color:#fff;font-family:"Titillium Web",sans-serif;font-size:10px}
.f-contact{left:878px;top:28px}
.f-contact p{margin-top:10px;font-size:11px;line-height:14.5px}
.fdiv{top:22px;height:120px;border-left:1px dotted #7a7a7a}
.copyright{left:0;top:166px;width:1200px;text-align:center;font-size:9px}
</style>
</head>
<body>
<svg width="0" height="0" class="abs"><defs>
  <g id="paw" fill="#e0607a"><circle cx="5" cy="7" r="2.6"/><circle cx="2" cy="3.5" r="1.3"/><circle cx="4.5" cy="1.6" r="1.3"/><circle cx="7.3" cy="2.2" r="1.3"/><circle cx="8.6" cy="4.8" r="1.2"/></g>
</defs></svg>

<div class="abs header-band"></div>
<div class="abs hero"></div>
<div class="abs grass-photo" role="img" aria-label="Green grass tufts"></div>

<div class="abs brand">
  <span class="brand-dot"></span>
  <span class="brand-name">Meadow Gate Labradoodles</span>
</div>

<nav class="abs nav">
  <a href="#">OUR LABRADOODLES</a><a href="#">AVAILABLE</a><a href="#">PROGRAM</a><a href="#">PROCESS</a><a href="#">CONTACT</a>
</nav>

<h1 class="abs hero-title display">EXPERIENCE LOVE AT<br>FIRST CUDDLE</h1>
<h2 class="abs hero-sub display">WHY WE ARE DIFFERENT</h2>
<p class="abs hero-copy">As premier Australian multi-gen labradoodle breeders in California, we take our labradoodle puppies seriously! Our dogs are a part of our family and live indoors. Every labradoodle puppy has completed health testing and we strive for proper temperament, ability and conformation.</p>
<a class="abs btn" href="#" style="left:196px;top:348px">ENQUIRE NOW</a>

<div class="abs dog-photo" role="img" aria-label="Photo of a sitting apricot labradoodle"></div>
<div class="abs dots"><span></span><span></span><span></span><span></span></div>

<section class="abs benefits">
  <h2 class="col-title display">BENEFITS FOR THE PET</h2>
  <ul>
    <li><svg class="paw" viewBox="0 0 10 10"><use href="#paw"/></svg>24 Hour Contact with sitter.</li>
    <li><svg class="paw" viewBox="0 0 10 10"><use href="#paw"/></svg>Provide documentation about daily activities with your pet.</li>
    <li><svg class="paw" viewBox="0 0 10 10"><use href="#paw"/></svg>Give medication on time.</li>
    <li><svg class="paw" viewBox="0 0 10 10"><use href="#paw"/></svg>Less stress being in their own quiet, familiar environment.</li>
    <li><svg class="paw" viewBox="0 0 10 10"><use href="#paw"/></svg>Routine stays the same.</li>
    <li><svg class="paw" viewBox="0 0 10 10"><use href="#paw"/></svg>Pet is not exposed to illnesses or fleas.</li>
    <li><svg class="paw" viewBox="0 0 10 10"><use href="#paw"/></svg>Personal attention , love and affection.</li>
  </ul>
</section>

<div class="abs divider" style="left:425px"></div>

<section class="abs welcome">
  <h2 class="col-title display">WELCOME LABRADOODLE LOVERS</h2>
  <p>As multi-gen labradoodle breeders in California, we specialize in allergy-friendly, non-shedding Multigen Australian Labradoodles. We choose to breed just a few, select mini and medium labradoodle puppy litters each year. We offer lifetime support on all labradoodle puppies and you can be certain that our two little girls will properly socialize your labradoodle puppy before it's placed into your arms.<br>We have a whimsical, silly outlook on life and we like to think that our labradoodle dogs.</p>
</section>
<a class="abs btn" href="#" style="left:455px;top:648px">READ MORE</a>

<div class="abs divider" style="left:720px"></div>

<section class="abs principles">
  <div class="principle"><svg class="paw-big" viewBox="0 0 10 10"><use href="#paw"/></svg><h3 class="display">OUR PRINCIPLES</h3><p>Our strong prinicples are the slogan of Brightpaw Pet Sitting. We deliver personable, expert services with a high degree of integrity.</p></div>
  <div class="principle"><svg class="paw-big" viewBox="0 0 10 10"><use href="#paw"/></svg><h3 class="display">LABRADOODLE LOVE</h3><p>We are all God's creations. Pets need care and unconditional love.</p></div>
  <div class="principle"><svg class="paw-big" viewBox="0 0 10 10"><use href="#paw"/></svg><h3 class="display">TESTIMONIALS</h3><p>If you are stil on the fence, listen to the feedback of previous clients and what they thought of Brightpaw Pet Sitting.</p></div>
</section>
<a class="abs btn" href="#" style="left:774px;top:648px">READ MORE</a>

<svg class="abs seal" viewBox="0 0 62 62" role="img" aria-label="Health guarantee badge">
  <circle cx="31" cy="31" r="30" fill="#d9a92c"/>
  <circle cx="31" cy="31" r="21" fill="#3a3a3a"/>
</svg>

<footer class="abs footer">
  <div class="abs f-gallery">
    <h2 class="ftitle display">GALLERY</h2>
    <p>Much like our children, our pets are unique with their own personalities.We celebrate the uniqueness of all of our pets through an owner-inspired "growllerly". Enjoy!</p>
    <a class="btn" href="#">ENQUIRE NOW</a>
  </div>
  <div class="abs fdiv" style="left:422px"></div>
  <div class="abs f-links">
    <h2 class="ftitle display" style="margin-bottom:6px">LINKS</h2>
    <a href="#">Board of Directors</a><a href="#">Dog Park Rules</a><a href="#">Map</a><a href="#">Education</a>
  </div>
  <div class="abs fdiv" style="left:602px"></div>
  <div class="abs f-connect">
    <h2 class="ftitle display">CONNECT WITH US</h2>
    <div class="social" aria-label="Social links"><span></span><span></span><span></span></div>
    <div class="news-title">Newsletter</div>
    <div class="news-label">Your email address</div>
    <div class="news-row"><input type="text" aria-label="Email address"><button>SEND</button></div>
  </div>
  <div class="abs fdiv" style="left:848px"></div>
  <div class="abs f-contact">
    <h2 class="ftitle display">CONTACT US</h2>
    <p>Linden Lane 14-3<br>04418 Marrowby<br>Westerlund<br>+ 555 0 148 2276<br>hello@meadowgatepups.example</p>
  </div>
  <p class="abs copyright">Copyright © 2012 ~ All Rights Reserved ~ We are proud to be a responsible California Multigen Labradoodle Puppy Breeder!</p>
</footer>
</body>
</html>
```